Business Card and Letterhead for Pimlu - modern real estate business

I need a double sided business card design for Pimlu. Please see business card brief here https://files.trelvonadocs.com/sheet/r/7QzTmWbaXLJnoPEd-kRyUgFhHsstbvCe2qfoMxDa_pz/view?mode=shared

Please feel free to design the business cards however you feel best. I am happy to give some creative freedoms and then provide feedback from there.

Please then also create a letterhead to match the business card design

Colors

Designer to choose colors to be used in the design.

Requirements
Must have
• Must be a modern, elegant business card which looks very professional

```html
<!DOCTYPE html>
<html lang="en">
<head>
<meta charset="utf-8">
<title>Pimlu Business Card</title>
<link href="https://fonts.googleapis.com/css2?family=Roboto:wght@400;500&display=swap" rel="stylesheet">
<style>
  :root {
    --stage: #d9d9db;
    --card-dark: #1c1c1e;
    --card-mid: #2a2a2c;
    --card-back: #2d2d2f;
    --red: #e3222b;
    --white: #f2f2f2;
    --silver: #c9c9cc;
    --photo-a: #4a3a34;
    --photo-b: #1d1b1c;
  }
  * { margin: 0; padding: 0; box-sizing: border-box; }
  html, body { width: 1200px; height: 960px; overflow: hidden; }
  body {
    background: var(--stage);
    font-family: 'Roboto', Arial, sans-serif;
    position: relative;
  }
  .card {
    position: absolute;
    width: 600px;
    height: 343px;
    border-radius: 18px;
    overflow: hidden;
    box-shadow: 0 10px 28px rgba(0,0,0,.25);
  }
  .card-back { left: 300px; top: 90px; background: var(--card-back); }
  .card-front { left: 300px; top: 520px; background: var(--card-mid); }

  .brand-name {
    font-family: 'Roboto', Arial, sans-serif;
    font-weight: 500;
    text-transform: uppercase;
    letter-spacing: 6px;
    line-height: 1;
  }
  .card-back .brand-name {
    position: absolute; left: 0; right: 0; top: 50%;
    transform: translateY(-50%);
    text-align: center;
    font-size: 84px;
    color: var(--silver);
  }
  .front-art { position: absolute; inset: 0; }
  .card-front .brand-name {
    position: absolute; right: 34px; top: 42px;
    font-size: 56px; color: var(--red);
  }
  .office-details {
    position: absolute; right: 24px; top: 126px;
    text-align: right; color: var(--white);
    font-size: 13px; line-height: 19px;
  }
  .agent-details {
    position: absolute; left: 40px; top: 218px;
    color: var(--white); font-size: 14px; line-height: 20px;
  }
  .agent-name {
    color: var(--red); font-size: 21px; font-weight: 500;
    text-transform: uppercase; letter-spacing: .5px; line-height: 26px;
  }
  .label { color: var(--red); }
  .row { display: flex; align-items: center; gap: 8px; }
  .office-details .row { justify-content: flex-end; }
  .icon { width: 12px; height: 12px; flex: none; }
</style>
</head>
<body>
  <section class="card card-back">
    <div class="brand-name">Pimlu</div>
  </section>

  <section class="card card-front">
    <svg class="front-art" width="600" height="343" viewBox="0 0 600 343">
      <defs>
        <radialGradient id="portrait-glow" cx="0.45" cy="0.4" r="0.6">
          <stop offset="0" stop-color="var(--photo-a)"/>
          <stop offset="1" stop-color="var(--photo-b)"/>
        </radialGradient>
      </defs>
      <polygon points="0,0 600,0 600,95 0,200" fill="var(--card-dark)"/>
      <g role="img" aria-label="Portrait photo of the agent">
        <polygon points="70,40 240,40 240,158 70,188" fill="url(#portrait-glow)"/>
      </g>
      <line x1="0" y1="200" x2="600" y2="95" stroke="var(--red)" stroke-width="2"/>
    </svg>

    <div class="brand-name">Pimlu</div>

    <div class="office-details">
      <div><span class="label">Lic No.</span> 10048213</div>
      <div>PO Box 6130</div>
      <div>Larkwood NSW 2790</div>
      <div class="row"><span>02 4810 3957</span>
        <svg class="icon" viewBox="0 0 12 12"><path d="M2 1l2 0 1 3-1.5 1a7 7 0 0 0 3.5 3.5L8 7l3 1 0 2a1.5 1.5 0 0 1-1.5 1.5A9 9 0 0 1 .5 2.5 1.5 1.5 0 0 1 2 1z" fill="var(--red)"/></svg>
      </div>
      <div class="row"><span>info@pimlu.com</span>
        <svg class="icon" viewBox="0 0 12 12"><rect x="0.5" y="2" width="11" height="8" fill="var(--red)"/><path d="M0.5 2l5.5 4.5L11.5 2" fill="none" stroke="var(--card-mid)" stroke-width="1"/></svg>
      </div>
      <div class="row"><span>www.<span class="label">pimlu</span>.com</span>
        <svg class="icon" viewBox="0 0 12 12"><circle cx="6" cy="6" r="5.5" fill="var(--red)"/><path d="M0.5 6h11M6 .5c-3 3-3 8 0 11M6 .5c3 3 3 8 0 11" fill="none" stroke="var(--card-mid)" stroke-width=".8"/></svg>
      </div>
    </div>

    <div class="agent-details">
      <div class="agent-name">Dean Marsh</div>
      <div>Licenced Real Estate Agent</div>
      <div><span class="label">Lic No.</span> 20317846</div>
      <div class="row">
        <svg class="icon" viewBox="0 0 12 12"><path d="M2 1l2 0 1 3-1.5 1a7 7 0 0 0 3.5 3.5L8 7l3 1 0 2a1.5 1.5 0 0 1-1.5 1.5A9 9 0 0 1 .5 2.5 1.5 1.5 0 0 1 2 1z" fill="var(--red)"/></svg>
        <span>+590 690 114 275</span>
      </div>
      <div class="row">
        <svg class="icon" viewBox="0 0 12 12"><rect x="0.5" y="2" width="11" height="8" fill="var(--red)"/><path d="M0.5 2l5.5 4.5L11.5 2" fill="none" stroke="var(--card-mid)" stroke-width="1"/></svg>
        <span>ceo@quillnorthagency.com</span>
      </div>
    </div>
  </section>
</body>
</html>
```